School Poster

Design so that these can be placed in classrooms across the school.

Attached is another design we have had done. Use a similar theme.

Consider using themes from https://corvalhs.edq.example.au/

please edit Binder1 doc.

Students and teachers

```html
<!DOCTYPE html>
<html lang="en">
<head>
<meta charset="utf-8">
<title>Classroom Posters</title>
<link rel="stylesheet" href="https://fonts.googleapis.com/css2?family=Poppins:wght@400;500;600;700;800;900&display=swap">
<style>
:root{
  --navy:#2c4599;
  --navy-dark:#263b8c;
  --yellow:#f3e97a;
  --grey:#e6e6e6;
  --red:#d22d35;
  --ink:#2a2a2a;
  --stage:#e8e9e8;
  --white:#ffffff;
  --divider:#bdbdbd;
}
*{box-sizing:border-box;margin:0;padding:0}
html,body{width:1200px;height:960px;overflow:hidden;background:var(--stage);font-family:'Poppins',sans-serif;color:var(--ink)}
.poster{position:absolute;top:144px;width:476px;height:672px;background:var(--navy)}
.poster--help{left:106px}
.poster--ai{left:618px}
.poster__header{position:absolute;left:0;top:0;width:100%;height:101px;background:var(--navy-dark)}
.poster__title{position:absolute;left:24px;top:20px;color:var(--white);font-weight:800;font-size:33px;line-height:33px;letter-spacing:.2px;text-transform:uppercase;white-space:nowrap}
.poster--help .poster__title{font-size:36px}
.school-mark{position:absolute;right:22px;top:26px;width:58px;display:flex;flex-direction:column;align-items:center;gap:4px}
.school-mark__dot{width:34px;height:34px;border-radius:50%;background:var(--yellow)}
.school-mark__name{color:var(--white);font-weight:700;font-size:9px;line-height:10px;text-align:center}
.strip{position:absolute;left:0;top:101px;width:100%;height:29px;background:var(--yellow)}
.strip__text{position:absolute;left:24px;top:0;line-height:29px;font-size:22px;font-weight:400;color:var(--ink)}
.strip--thin{height:10px}
.panel{position:absolute;left:10px;width:456px;background:var(--white);border-radius:8px;overflow:hidden}
.poster--help .panel{top:140px;height:520px}
.poster--ai .panel{top:130px;height:507px}

/* steps */
.step{position:absolute;top:26px;width:138px;height:416px;border:2px solid var(--navy);border-radius:10px}
.step--1{left:13px}.step--2{left:159px}.step--3{left:306px}
.step__num{position:absolute;left:50%;top:-14px;transform:translateX(-50%);width:34px;height:26px;background:var(--white);display:flex;justify-content:center}
.step__num span{width:24px;height:24px;border-radius:50%;background:var(--navy);color:var(--white);font-weight:800;font-size:15px;line-height:24px;text-align:center}
.step__art{position:absolute;left:24px;top:24px;width:88px;height:86px;border-radius:12px;background:linear-gradient(135deg,#dfe4f4,#f6f0b8)}
.step__name{position:absolute;left:0;top:118px;width:100%;height:76px;display:flex;align-items:center;justify-content:center;text-align:center;color:var(--navy);font-weight:900;font-size:19px;line-height:19px}
.step__lead{position:absolute;left:0;top:192px;width:100%;height:46px;background:var(--yellow);display:flex;align-items:center;justify-content:center;text-align:center;color:var(--navy);font-weight:700;font-size:12px;line-height:13px;padding:0 5px}
.step__body{position:absolute;left:0;top:238px;width:100%;height:176px;background:var(--grey);padding:8px 6px 0 10px;border-radius:0 0 8px 8px}
.step__list{list-style:none}
.step__list li{position:relative;padding-left:10px;font-size:10px;line-height:13.5px;margin-bottom:3px;color:var(--ink)}
.step__list li::before{content:"";position:absolute;left:0;top:5px;width:4px;height:4px;border-radius:50%;background:var(--navy)}
.step__then{font-weight:700;font-size:10px;line-height:13.5px;margin-top:3px}
.step__motto{position:absolute;left:50%;bottom:-14px;transform:translateX(-50%);width:112px;height:26px;border-radius:8px;background:var(--navy);color:var(--white);font-weight:900;font-size:15px;line-height:26px;text-align:center;white-space:nowrap}
.step__motto b{color:var(--yellow);font-weight:900}
.refs{position:absolute;left:0;bottom:0;width:100%;height:51px;background:var(--yellow);padding:8px 27px;font-size:5px;line-height:6.4px;color:#333}
.refs strong{display:block;font-size:5.5px}

/* ai poster */
.section-title{position:absolute;left:0;width:100%;text-align:center;color:var(--navy);font-weight:900;font-size:19px;line-height:22px}
.musts{position:absolute;top:38px;list-style:none}
.musts--a{left:22px;width:182px}
.musts--b{left:208px;width:128px}
.musts li{position:relative;padding-left:15px;font-weight:700;font-size:11px;line-height:13.5px;margin-bottom:5px;color:var(--ink)}
.musts svg{position:absolute;left:0;top:3px}
.ai-art{position:absolute;left:340px;top:25px;width:102px;height:107px;border-radius:14px;background:linear-gradient(135deg,#dfe4f4,#f6f0b8)}
.helps{position:absolute;left:14px;top:138px;width:427px;height:197px;background:var(--yellow);border-radius:8px}
.helps__sub{position:absolute;left:0;top:29px;width:100%;text-align:center;font-size:12px;color:var(--navy)}
.grid4{position:absolute;left:0;display:flex;width:100%}
.grid4__cell{position:relative;flex:1;display:flex;flex-direction:column;align-items:center;text-align:center}
.grid4__cell+.grid4__cell::before{content:"";position:absolute;left:0;top:0;bottom:0;width:1px;background:var(--divider)}
.helps .grid4{top:58px;height:130px}
.helps__art{width:64px;height:64px;border-radius:10px;background:linear-gradient(135deg,#c9d1ec,#e9e3a0)}
.helps__label{margin-top:18px;font-weight:700;font-size:11px;line-height:12.5px;color:var(--ink);padding:0 8px}
.nots{top:384px;height:124px}
.nots__label{margin-top:8px;font-weight:700;font-size:11px;line-height:12.7px;color:var(--ink);padding:0 9px}
.poster__footer{position:absolute;left:0;top:641px;width:100%;text-align:center;color:var(--white);font-weight:700;font-size:11px}
</style>
</head>
<body>

<section class="poster poster--help">
  <header class="poster__header">
    <h1 class="poster__title">Before you ask<br>the teacher...</h1>
    <div class="school-mark"><span class="school-mark__dot"></span><span class="school-mark__name">Corval SHS</span></div>
  </header>
  <div class="strip"><p class="strip__text">TRY THESE STEPS FIRST!</p></div>
  <div class="panel">
    <article class="step step--1">
      <div class="step__num"><span>1</span></div>
      <div class="step__art" role="img" aria-label="Head with a lightbulb idea icon"></div>
      <h2 class="step__name">THINK<br>FIRST</h2>
      <p class="step__lead">Don't give up straight away.</p>
      <div class="step__body">
        <ul class="step__list">
          <li>Read the question carefully.</li>
          <li>Identify what you already know.</li>
          <li>Try a strategy you've used before.</li>
          <li>Give yourself thinking time.</li>
        </ul>
      </div>
      <div class="step__motto">WE <b>BELIEVE</b></div>
    </article>
    <article class="step step--2">
      <div class="step__num"><span>2</span></div>
      <div class="step__art" role="img" aria-label="Clipboard checklist icon"></div>
      <h2 class="step__name">CHECK<br>YOUR<br>SUPPORTS</h2>
      <p class="step__lead">Before asking for help, check:</p>
      <div class="step__body">
        <ul class="step__list">
          <li>Learning goal and success criteria.</li>
          <li>Worked examples.</li>
          <li>Class notes.</li>
          <li>Classroom displays.</li>
          <li>LearnHub resources.</li>
          <li>Task sheet and instructions.</li>
        </ul>
      </div>
      <div class="step__motto">WE <b>STRIVE</b></div>
    </article>
    <article class="step step--3">
      <div class="step__num"><span>3</span></div>
      <div class="step__art" role="img" aria-label="Group of three people with speech bubbles icon"></div>
      <h2 class="step__name">ASK 3<br>BEFORE ME</h2>
      <p class="step__lead">Ask three sources before asking the teacher:</p>
      <div class="step__body">
        <ul class="step__list">
          <li>A person (partner or neighbour)</li>
          <li>A place (notes, display, LearnHub)</li>
          <li>A resource (worked example, task sheet)</li>
        </ul>
        <p class="step__then">Then ask the teacher if you still need help.</p>
      </div>
      <div class="step__motto">WE <b>ACHIEVE</b></div>
    </article>
    <footer class="refs">
      <strong>References</strong>
      Hallworth, M. (2025). Helping Students Feel Ready to Ask for Help. Classnotes Journal. Downloaded 24/04/2026 from:<br>
      https://www.classnotes.example.org/asking-for-help/<br>
      Learning Evidence Institute. (2024). Supporting Self-Regulated Learning. Downloaded 24/04/2026 from:<br>
      https://www.learnevidence.example.au/self-regulated-learning.pdf
    </footer>
  </div>
</section>

<section class="poster poster--ai">
  <header class="poster__header">
    <h1 class="poster__title">Using AI and other<br>tools responsibly</h1>
    <div class="school-mark"><span class="school-mark__dot"></span><span class="school-mark__name">Corval SHS</span></div>
  </header>
  <div class="strip strip--thin"></div>
  <div class="panel">
    <h2 class="section-title" style="top:7px">WHAT YOU MUST DO:</h2>
    <ul class="musts musts--a">
      <li><svg width="8" height="8" viewBox="0 0 8 8"><rect x=".5" y=".5" width="7" height="7" fill="none" stroke="#2c4599"/><path d="M1.8 4l1.5 1.5 3-3.2" fill="none" stroke="#2c4599"/></svg>Complete your own work</li>
      <li><svg width="8" height="8" viewBox="0 0 8 8"><rect x=".5" y=".5" width="7" height="7" fill="none" stroke="#2c4599"/><path d="M1.8 4l1.5 1.5 3-3.2" fill="none" stroke="#2c4599"/></svg>Demonstrate your progress (drafts, notes, planning, revisions)</li>
      <li><svg width="8" height="8" viewBox="0 0 8 8"><rect x=".5" y=".5" width="7" height="7" fill="none" stroke="#2c4599"/><path d="M1.8 4l1.5 1.5 3-3.2" fill="none" stroke="#2c4599"/></svg>Use feedback to improve your work</li>
    </ul>
    <ul class="musts musts--b">
      <li><svg width="8" height="8" viewBox="0 0 8 8"><rect x=".5" y=".5" width="7" height="7" fill="none" stroke="#2c4599"/><path d="M1.8 4l1.5 1.5 3-3.2" fill="none" stroke="#2c4599"/></svg>Demonstrate your understanding of the ideas in your submission</li>
    </ul>
    <div class="ai-art" role="img" aria-label="Brain with circuit lines and AI chip illustration"></div>

    <div class="helps">
      <h2 class="section-title" style="top:7px">WHAT AI CAN HELP YOU DO</h2>
      <p class="helps__sub">(when approved by your teacher)</p>
      <div class="grid4">
        <div class="grid4__cell"><div class="helps__art" role="img" aria-label="Brain icon"></div><p class="helps__label">Brainstorm<br>ideas</p></div>
        <div class="grid4__cell"><div class="helps__art" role="img" aria-label="Checklist with magnifier icon"></div><p class="helps__label">Check spelling, grammar and clarity</p></div>
        <div class="grid4__cell"><div class="helps__art" role="img" aria-label="Phone with speaking head icon"></div><p class="helps__label">Read your work aloud using text-to-speech tools</p></div>
        <div class="grid4__cell"><div class="helps__art" role="img" aria-label="Rising bar chart with gear icon"></div><p class="helps__label">Help identify areas for improvement in a draft</p></div>
      </div>
    </div>

    <h2 class="section-title" style="top:346px">WHAT YOU CANNOT DO:</h2>
    <div class="grid4 nots">
      <div class="grid4__cell"><svg width="38" height="38" viewBox="0 0 38 38"><circle cx="19" cy="19" r="16" fill="none" stroke="#d22d35" stroke-width="3"/><path d="M13 12l12 14M25 12L13 26" stroke="#d22d35" stroke-width="3" stroke-linecap="round"/></svg><p class="nots__label">Submit AI-generated work as your own</p></div>
      <div class="grid4__cell"><svg width="38" height="38" viewBox="0 0 38 38"><circle cx="19" cy="19" r="16" fill="none" stroke="#d22d35" stroke-width="3"/><path d="M13 12l12 14M25 12L13 26" stroke="#d22d35" stroke-width="3" stroke-linecap="round"/></svg><p class="nots__label">Copy and paste AI responses without acknowledging or adapting them</p></div>
      <div class="grid4__cell"><svg width="38" height="38" viewBox="0 0 38 38"><circle cx="19" cy="19" r="16" fill="none" stroke="#d22d35" stroke-width="3"/><path d="M13 12l12 14M25 12L13 26" stroke="#d22d35" stroke-width="3" stroke-linecap="round"/></svg><p class="nots__label">Use AI tools to complete the whole task for you</p></div>
      <div class="grid4__cell"><svg width="38" height="38" viewBox="0 0 38 38"><circle cx="19" cy="19" r="16" fill="none" stroke="#d22d35" stroke-width="3"/><path d="M13 12l12 14M25 12L13 26" stroke="#d22d35" stroke-width="3" stroke-linecap="round"/></svg><p class="nots__label">Submit work that does not demonstrate your understanding</p></div>
    </div>
  </div>
  <p class="poster__footer">If you didn't create, develop and understand it, it isn't your work.</p>
</section>

</body>
</html>
```